Business card design for Automotive workshop

We need a business card for a new automotive repair and tyre shop called Keelstone Prime Automotive located in New Zealand. We are a clean, modern and fresh workshop and company.

Front needs to feature logo,
my name:
Marlo Fenwicke (director)

Address:
48 Tarn Lane
Korimako Bay 3579

Phone: 07 594 2713
Mobile: 027 451 9362
Email: office@keelstoneautomotive.example.nz
Website: keelstoneautomotive.example.nz

Back needs to feature an area to write down appointment details, date and time.

Also feature a list of jobs and work we do such as,
Vehicle Servicing
All Mechanical Repairs
Warrant of Fitness
Tyres & Wheel Alignments
Automotive Diagnostics
Automotive Parts & Supplies

```html
<!DOCTYPE html>
<html lang="en">
<head>
<meta charset="utf-8">
<title>Keelstone Prime Automotive – Business Card</title>
<link href="https://fonts.googleapis.com/css2?family=Exo+2:ital,wght@0,400;0,600;0,700;1,400&family=Ubuntu:wght@400;500&display=swap" rel="stylesheet">
<style>
  :root {
    --stage: #2b2e32;
    --ink: #111214;
    --red: #e31b23;
    --paper: #ffffff;
    --text: #1d1d1f;
    --dash: #555a60;
  }
  * { margin: 0; padding: 0; box-sizing: border-box; }
  html, body { width: 1200px; height: 900px; overflow: hidden; }
  body {
    background: var(--stage);
    font-family: "Ubuntu", sans-serif;
    position: relative;
  }
  .card {
    position: absolute;
    top: 296px;
    width: 540px;
    height: 309px;
    background: var(--paper);
    overflow: hidden;
    box-shadow: 0 14px 30px rgba(0,0,0,.45);
  }
  .card--front { left: 40px; }
  .card--back { left: 620px; }
  .card__shapes { position: absolute; inset: 0; width: 100%; height: 100%; }

  /* Wordmark */
  .wordmark {
    font-family: "Exo 2", sans-serif;
    font-weight: 700;
    color: var(--red);
    text-transform: uppercase;
    line-height: 1;
    letter-spacing: .04em;
    white-space: nowrap;
  }
  .card--front .wordmark {
    position: absolute;
    left: 75px;
    top: 154px;
    transform: translate(-50%, -50%) rotate(-90deg);
    font-size: 24px;
    text-align: center;
  }
  .wordmark__sub { display: block; font-size: .62em; letter-spacing: .3em; margin-top: 6px; }

  /* Front content */
  .contact {
    position: absolute;
    left: 196px;
    top: 58px;
  }
  .contact__name {
    font-family: "Exo 2", sans-serif;
    font-weight: 700;
    font-size: 24px;
    color: var(--red);
    text-transform: uppercase;
    letter-spacing: .03em;
  }
  .contact__role { font-size: 14px; color: var(--text); margin-top: 2px; }
  .contact__list { list-style: none; margin-top: 18px; }
  .contact__list li {
    display: flex; align-items: center; gap: 9px;
    font-size: 14.5px; color: var(--text); line-height: 1.5;
  }
  .contact__list svg { width: 13px; height: 13px; flex: none; }
  .contact__address { margin-top: 14px; font-size: 15px; color: var(--red); }

  /* Back content */
  .card--back .wordmark {
    position: absolute; right: 26px; top: 22px;
    font-size: 24px; text-align: right;
  }
  .services {
    position: absolute; list-style: none;
    font-family: "Exo 2", sans-serif; font-style: italic;
    font-size: 12px; color: var(--text); text-transform: uppercase; line-height: 1.45;
  }
  .services--left { left: 26px; top: 66px; }
  .services--right { right: 22px; top: 176px; text-align: right; }
  .services li::before, .services--right li::after {
    content: ""; display: inline-block; width: 6px; height: 6px;
    border-radius: 50%; background: var(--red); vertical-align: middle;
  }
  .services--left li::before { margin-right: 7px; }
  .services--right li::before { display: none; }
  .services--right li::after { margin-left: 7px; }
  .appt-label {
    position: absolute;
    font-family: "Exo 2", sans-serif; font-style: italic;
    font-size: 12px; color: var(--red); text-transform: uppercase;
  }
  .appt-label--date { left: 20px; top: 140px; }
  .appt-label--time { left: 196px; top: 240px; }
</style>
</head>
<body>

<article class="card card--front" aria-label="Business card front">
  <svg class="card__shapes" viewBox="0 0 540 309" aria-hidden="true">
    <rect x="0" y="0" width="152" height="309" fill="var(--ink)"/>
    <rect x="163" y="0" width="5" height="309" fill="var(--red)"/>
  </svg>
  <div class="wordmark">Keelstone Prime<span class="wordmark__sub">Automotive</span></div>

  <div class="contact">
    <h1 class="contact__name">Marlo Fenwicke</h1>
    <p class="contact__role">Director</p>
    <ul class="contact__list">
      <li>
        <svg viewBox="0 0 16 16"><circle cx="8" cy="8" r="7" fill="none" stroke="var(--red)" stroke-width="1.5"/><path d="M5.5 4.5l1.5 1.5-1 1c.5 1 1.5 2 2.5 2.5l1-1 1.5 1.5-1 1.2C7.5 11 5 8.5 4.8 6z" fill="var(--red)"/></svg>
        07 594 2713
      </li>
      <li>
        <svg viewBox="0 0 16 16"><rect x="4" y="1" width="8" height="14" rx="1.5" fill="none" stroke="var(--red)" stroke-width="1.5"/><circle cx="8" cy="12.5" r=".9" fill="var(--red)"/></svg>
        027 451 9362
      </li>
      <li>
        <svg viewBox="0 0 16 16"><rect x="1" y="3" width="14" height="10" fill="none" stroke="var(--red)" stroke-width="1.5"/><path d="M1 3l7 6 7-6" fill="none" stroke="var(--red)" stroke-width="1.5"/></svg>
        office@keelstoneautomotive.example.nz
      </li>
      <li>
        <svg viewBox="0 0 16 16"><circle cx="8" cy="8" r="7" fill="var(--red)"/><path d="M1 8h14M8 1c-3 3.5-3 10.5 0 14M8 1c3 3.5 3 10.5 0 14" fill="none" stroke="#fff" stroke-width="1"/></svg>
        keelstoneautomotive.example.nz
      </li>
    </ul>
    <p class="contact__address">48 Tarn Lane, Korimako Bay 3579</p>
  </div>
</article>

<article class="card card--back" aria-label="Business card back">
  <svg class="card__shapes" viewBox="0 0 540 309" aria-hidden="true">
    <polygon points="0,0 170,0 0,38" fill="var(--red)"/>
    <polygon points="190,0 540,0 540,118 250,52 0,62 0,48" fill="var(--ink)"/>
    <polygon points="0,150 60,160 0,178" fill="var(--ink)"/>
    <polygon points="0,160 40,160 0,172" fill="var(--red)"/>
    <g stroke="var(--dash)" stroke-width="1" stroke-dasharray="6 5">
      <line x1="60" y1="124" x2="360" y2="124"/>
      <line x1="64" y1="154" x2="330" y2="154"/>
      <line x1="20" y1="186" x2="300" y2="186"/>
      <line x1="20" y1="218" x2="300" y2="218"/>
      <line x1="236" y1="252" x2="520" y2="252"/>
      <line x1="196" y1="282" x2="520" y2="282"/>
    </g>
  </svg>
  <div class="wordmark">Keelstone Prime<span class="wordmark__sub">Automotive</span></div>

  <ul class="services services--left">
    <li>Vehicle Servicing</li>
    <li>All Mechanical Repairs</li>
    <li>Warrant of Fitness</li>
  </ul>
  <ul class="services services--right">
    <li>Tyres &amp; Wheel Alignments</li>
    <li>Automotive Diagnostics</li>
    <li>Automotive Parts &amp; Supplies</li>
  </ul>
  <span class="appt-label appt-label--date">Date:</span>
  <span class="appt-label appt-label--time">Time:</span>
</article>

</body>
</html>
```